Brochure for a civil enineering company in A4 format

I need a brochure design for our company TIRO Engineering S.r.l.. We are an engineering consultant company. Our main clients are from the infrastructure industry (geotechnical and underground sectors mainly).
We are looking for a 2 pages (4 faces) fold out design with a glued pocket where we can put individual data sheets.
I need A4 format pages.

Target Market(s)

We are an engineering consultant company. Our main clients are from the infrastructure industry (geotechnical and underground sectors mainly).

Industry/Entity Type

Civil Engineer

Font styles to use
Sans Serif

Requirements
Must have
• Overall: 2 pages in A4 format
Essential style. Bright and modern appearance.
Glued pocket
Logo integrated in a picture on the pocket where I would like to insert a slogan (… tiro engineering … reliable solutions …)
Attached are selected images which the designer can use and edit at their own discretion.
Some advice in the following (anyway designers are free to provide their solutions):
Outer sheets:
Front page with name, logo. It could be nice to have the “m” of the logo integrated in a pictures, also a modified picture (I mean modify one of the attached pictures) so to create a general image and do not tie the cover to a specific job.
Back page: offices address and contact email address. Nice to have one space for a slogan.
Inner sheet: text that I upload in the file “inside-sheets”, possibly with pictures on each sheet. In the right faces insert the glued pocket. On this pages insert the section OUR EXPERIENCE ….with a space for a picture of our team.
Nice to have
• Clean and essential design.
Pictures choosing from the atteched ones. Pictures could be modified in a very light manner to make them a general idea of the work ( I mean geotechnical world) without to be immediately linked to a specific site.
Should not have
• excessive frills

```html
<!DOCTYPE html>
<html lang="it">
<head>
<meta charset="utf-8">
<title>TIRO Engineering – Brochure interno</title>
<link rel="stylesheet" href="https://fonts.googleapis.com/css2?family=Roboto:wght@300;400;700&family=Open+Sans:wght@400&display=swap">
<style>
  :root{
    --blue:#0b6fb8;
    --blue-deep:#0a5fa0;
    --ink:#1b1b1b;
    --body:#2b2b2b;
    --dark-band:#232323;
    --panel-grey:#c8c8ca;
    --page:#ffffff;
    --backdrop:#f1f1f1;
  }
  *{margin:0;padding:0;box-sizing:border-box}
  html,body{width:1200px;height:1200px;overflow:hidden;background:var(--backdrop)}
  .spread{position:absolute;left:20px;top:187px;width:1160px;height:826px;background:var(--page);overflow:hidden;font-family:"Roboto",sans-serif;color:var(--body)}
  .hero-photo{position:absolute;left:0;top:0;width:848px;height:439px;
    background:linear-gradient(160deg,#3d98d6 0%,#2a86cc 45%,#5aa9dc 70%,#8aa4b4 100%)}
  .hero-tint{position:absolute;left:580px;top:0;width:268px;height:439px;background:rgba(11,111,184,.35)}
  .expertise-band{position:absolute;left:0;top:313px;width:410px;height:85px}
  .expertise-title{position:absolute;left:26px;top:325px;color:#fff;line-height:1}
  .expertise-title .light{font-weight:300;font-size:21px;display:block}
  .expertise-title .bold{font-weight:700;font-size:35px;display:block;margin-top:6px;letter-spacing:.5px}
  .slogan{position:absolute;left:611px;top:285px;color:#fff;font-weight:700;line-height:1}
  .slogan span{display:block}
  .slogan .s1{font-size:21px}
  .slogan .s2{font-size:21px;margin-top:3px}
  .slogan .s3{font-size:33px;margin-top:4px}
  .story{position:absolute;left:8px;top:398px;width:572px;height:404px;background:var(--page);padding:0 8px 0 0}
  .story p{font-weight:300;font-size:9.1px;line-height:11.5px;text-align:justify;margin-bottom:11.5px;letter-spacing:-.1px}
  .company{position:absolute;left:848px;top:0;width:312px;height:439px;background:var(--page)}
  .section-title{font-weight:400;font-size:28px;color:var(--ink);line-height:1}
  .section-title em{font-style:normal;color:var(--blue)}
  .company .section-title{position:absolute;left:20px;top:33px}
  .company .copy{position:absolute;left:20px;top:93px;width:250px}
  .company .copy p{font-weight:300;font-size:9.1px;line-height:11.5px;text-align:justify;margin-bottom:7px;letter-spacing:-.1px}
  .company .copy p.tight{margin-bottom:0}
  .company .staff-title{position:absolute;left:20px;top:400px}
  .staff-panel{position:absolute;left:580px;top:439px;width:580px;height:363px;background:var(--panel-grey)}
  .portrait{position:absolute;top:32px;width:158px;height:130px;
    background:linear-gradient(180deg,#e4e4e4 0%,#d6d6d6 60%,#b9bcbf 100%)}
  .pocket{position:absolute;left:17px;top:185px;width:547px;height:169px;border:1.3px dashed #222;border-radius:4px;background:var(--page)}
  .pocket-label{position:absolute;left:50px;top:177px;width:119px;height:18px;border:1px solid #222;background:#fff;
    font-size:13.5px;line-height:16px;text-align:center;color:var(--ink)}
  .member{position:absolute;top:210px;width:160px;font-family:"Open Sans",sans-serif;color:var(--ink)}
  .member h3{font-family:"Roboto",sans-serif;font-weight:400;font-size:17.5px;line-height:20px;margin-bottom:16px}
  .member p{font-size:10.2px;line-height:11.5px}
  .foot-band{position:absolute;top:802px;height:24px}
  .foot-band.blue-left{left:0;width:321px;background:var(--blue)}
  .foot-band.dark{left:321px;width:518px;background:var(--dark-band)}
  .foot-band.blue-right{left:839px;width:321px;background:var(--blue)}
</style>
</head>
<body>
<main class="spread">
  <div class="hero-photo" role="img" aria-label="Fotografia di cantiere: scudo di una fresa TBM sollevato da una grande gru cingolata rossa contro un cielo azzurro"></div>
  <div class="hero-tint"></div>

  <svg class="expertise-band" viewBox="0 0 410 85" aria-hidden="true">
    <polygon points="0,0 278,0 410,85 0,85" fill="var(--blue)"/>
  </svg>
  <h2 class="expertise-title"><span class="light">OUR EXPERTISE</span><span class="bold">AND EXPERIENCE</span></h2>

  <p class="slogan"><span class="s1">WE</span><span class="s2">BUILD BETTER</span><span class="s3">FOR YOU</span></p>

  <section class="story">
    <p>La società nasce dall’associazione di un gruppo di professionisti, con indiscusse competenze ed affidabilità, con esperienza maturata in oltre trent’anni di attività come progettisti e consulenti nel settore delle grandi opere di ingegneria civile; geologia, ingegneria geotecnica ed idraulica ed opere sotterranee sono il “core” delle loro competenze ....</p>
    <p>I soci fondatori sono:</p>
    <p>Marco. Già Direttore Tecnico e Socio di VESTA Srl, nel periodo di sua permanenza fino al dicembre 2018, ha per essa firmato tutti i progetti nel campo delle opere sotterranee e la maggior parte di quelli di ingegneria geotecnica. Da gennaio 2019 è Direttore Tecnico di GEOPRO. Può vantare più di 150 gallerie naturali, e numerosi progetti ed assistenze tecniche nel campo delle strutture geotecniche, delle sistemazioni idrogeologiche e dei versanti e delle opere di protezione ambientale. Negli ultimi dieci anni è stato responsabile di attività di assistenza tecnica, per imprese di costruzione, di opere il cui valore supera i 440 Mio EUR e di servizi di progettazione definitiva e/o esecutiva per opere il cui valore supera i 1.400 Mio EUR. Ha svolto attività di verifica e validazione, in Italia ed all’estero, di numerosi progetti il cui valore complessivo supera i 3.400 Mio EUR.</p>
    <p>Enzo 30 anni di esperienza professionale. Coinvolto in più di 150 gallerie naturali con lunghezza complessiva superiore a 360 km. Numerosi progetti ed attività di assistenza tecnica nel campo delle strutture, delle sistemazioni idrogeologiche e dei versanti e delle opere di protezione ambientale. Negli ultimi dieci anni responsabile di attività di assistenza tecnica in corso d’opera, per imprese di costruzione, di opere il cui valore supera i 440 Mio EUR e di servizi di progettazione definitiva o esecutiva per opere il cui valore supera i 1.400 Mio EUR. Ha svolto attività di verifica ai fini della validazione, in Italia ed all’estero, di numerosi progetti il cui valore complessivo supera i 3.400 Mio EUR.</p>
    <p>Giulia 30 anni di esperienza professionale. Coinvolto in più di 150 gallerie naturali con lunghezza complessiva superiore a 360 km. Numerosi progetti ed attività di assistenza tecnica nel campo delle strutture, delle sistemazioni idrogeologiche e dei versanti e delle opere di protezione ambientale. Negli ultimi dieci anni responsabile di attività di assistenza tecnica in corso d’opera, per imprese di costruzione, di opere il cui valore supera i 440 Mio EUR e di servizi di progettazione definitiva o esecutiva per opere il cui valore supera i 1.400 Mio EUR. Ha svolto attività di verifica ai fini della validazione, in Italia ed all’estero, di numerosi progetti il cui valore complessivo supera i 3.400 Mio EUR.</p>
    <p>Chiara 30 anni di esperienza professionale. Coinvolto in più di 150 gallerie naturali con lunghezza complessiva superiore a 360 km. Numerosi progetti ed attività di assistenza tecnica nel campo delle strutture, delle sistemazioni idrogeologiche e dei versanti e delle opere di protezione ambientale. Negli ultimi dieci anni responsabile di attività di assistenza tecnica in corso d’opera, per imprese di costruzione, di opere il cui valore supera i 440 Mio EUR e di servizi di progettazione definitiva o esecutiva per opere il cui valore supera i 1.400 Mio EUR. Ha svolto attività di verifica ai fini della validazione, in Italia ed all’estero, di numerosi progetti il cui valore complessivo supera i 3.400 Mio EUR.</p>
  </section>

  <section class="company">
    <h2 class="section-title">Our <em>Company</em></h2>
    <div class="copy">
      <p>TIRO Engineering S.r.l. offre servizi di consulenza tecnica, contrattuale e strategica ai principali attori nei settori delle scienze geologiche, dell’ingegneria geotecnica e dell’ingegneria idraulica. Lavoriamo per mitigare il rischio e ridurre l’incertezza, con flessibilità nella ricerca della soluzione ottimale contribuendo ad aumentare la redditività del progetto.</p>
      <p>TIRO Engineering S.r.l. è una società indipendente che nasce nel luglio 2020 dall’associazione di un gruppo di professionisti che hanno messo a fattor comune la reciproca esperienza maturata in oltre trent’anni di attività come progettisti e consulenti nel settore delle grandi opere di ingegneria civile lavorando come Direttori Tecnici di Main Engineering Companies and as Freelancers.</p>
      <p class="tight">TIRO Engineering S.r.l. vuole unire l’esperienza dei Fondatori e delle figure chiave con l’entusiasmo di chi intraprende una nuova attività, per dare vita ad una nuova realtà che si pone come obbiettivo principale il design of infrastructures that are safe, sustainable and economic.</p>
      <p>Each of our projects represents a long term commitment, we believe in providing safe, reliable, sustainable end innovative solutions. This is and will be our distinctive characteristic.</p>
    </div>
    <h2 class="section-title staff-title">Meet Our <em>Staff</em></h2>
  </section>

  <section class="staff-panel">
    <div class="portrait" style="left:29px" role="img" aria-label="Ritratto fotografico di un membro del team su fondo grigio chiaro"></div>
    <div class="portrait" style="left:206px" role="img" aria-label="Ritratto fotografico di una collega su fondo bianco"></div>
    <div class="portrait" style="left:383px" role="img" aria-label="Ritratto fotografico di un membro del team su fondo bianco"></div>

    <div class="pocket"></div>
    <div class="pocket-label">Glued Pocket Here</div>

    <article class="member" style="left:29px">
      <h3>Luca B., MSc.</h3>
      <p>Donec tincidunt placerat nisl egetat dapibus.Integer sapien For aliquam arcu,aliquam sit amet blandit ut, of facilisis sed tortor. Donec at finibus tortor. Etiam posuere congue risus, ac fringilla elit tincidunt in.</p>
    </article>
    <article class="member" style="left:206px">
      <h3>Sara T., MBA</h3>
      <p>Donec tincidunt placerat nisl egetat dapibus.Integer sapien For aliquam arcu,aliquam sit amet blandit ut, of facilisis sed tortor. Donec at finibus tortor. Etiam posuere congue risus, ac fringilla elit tincidunt in.</p>
    </article>
    <article class="member" style="left:383px">
      <h3>Peter Vance, MT.</h3>
      <p>Donec tincidunt placerat nisl egetat dapibus.Integer sapien For aliquam arcu,aliquam sit amet blandit ut, of facilisis sed tortor. Donec at finibus tortor. Etiam posuere congue risus, ac fringilla elit tincidunt in.</p>
    </article>
  </section>

  <div class="foot-band blue-left"></div>
  <div class="foot-band dark"></div>
  <div class="foot-band blue-right"></div>
</main>
</body>
</html>
```